Rack card 4"x9" for a construction company

We need to have a design for:
- the holder of rack cards. Letter size
- and the rack cards. Size 4"x9"

I attached a picture of the sample holder for example.

I am putting some of the brochures and pics we have in:

https://files.example-share.net/folders/7Qw3ZtR9pLx2MvB8nKd4YsH1cFj6GaUeT?usp=sharing

The Bodoni font is on the drive.
The rack card should call to action - to learn about our projects and that we are offering fixed price packages.

One of the sides of the rack card has to show our houses like we show on the website brindle-homes.ca
Images with short info like on the website http://www.brindle-homes.ca/our-projects/
Maybe have something like: Learn more about our recent projects at www...

You can use our logo from th pdf files. In the brochure on the cover page we show all the associations we are member of - this is a must to be shown.

Mentioning the website and the phone number is a must.

Bring your ideas.
Don't hesitate to ask questions.

Thanks
Marcus

```html
<!DOCTYPE html>
<html lang="en">
<head>
<meta charset="utf-8">
<title>Brindle Homes – Rack Card</title>
<link href="https://fonts.googleapis.com/css2?family=Bodoni+Moda:ital,wght@0,500;0,700;1,500&family=Open+Sans:wght@300;400;600&display=swap" rel="stylesheet">
<style>
  :root {
    --navy: #1b2848;
    --tan: #bdaf8c;
    --paper: #f3f2ef;
    --ink: #2a2f3a;
    --muted: #6d7079;
    --stage: #9ba4b2;
    --sky: #9fc4e0;
    --leaf: #5d7f3f;
    --stone: #5a5f66;
  }
  * { box-sizing: border-box; margin: 0; padding: 0; }
  html, body { width: 1200px; height: 961px; overflow: hidden; }
  body { background: var(--stage); font-family: "Open Sans", sans-serif; color: var(--ink); position: relative; }

  .rack-card { position: absolute; left: 100px; width: 1000px; height: 444px; background: var(--paper); overflow: hidden; box-shadow: 0 6px 18px rgba(30,40,60,.25); }
  .rack-card--back { top: 24px; }
  .rack-card--front { top: 493px; }

  .photo { background: linear-gradient(180deg, var(--sky) 0%, #c9d8e4 40%, var(--stone) 62%, var(--leaf) 100%); }

  /* Project side */
  .projects { display: flex; height: 400px; }
  .project { flex: 1; border-right: 10px solid var(--paper); position: relative; }
  .project:last-child { border-right: 0; }
  .project__photo { height: 200px; }
  .project__label { position: relative; background: var(--navy); color: #fff; font-family: "Bodoni Moda", serif; font-weight: 700; font-size: 17px; text-align: center; padding: 12px 8px; white-space: nowrap; }
  .project__label::after { content: ""; position: absolute; left: 50%; bottom: -12px; margin-left: -14px; border-left: 14px solid transparent; border-right: 14px solid transparent; border-top: 12px solid var(--navy); }
  .project__specs { list-style: none; text-align: center; font-family: "Bodoni Moda", serif; font-size: 14px; color: var(--muted); line-height: 1.55; padding-top: 22px; }
  .project__specs .total { color: var(--ink); font-weight: 700; }
  .back-footer { position: absolute; left: 0; right: 0; bottom: 0; height: 44px; display: flex; }
  .back-footer__spacer { flex: 1; }
  .back-footer__web { background: var(--tan); color: #fff; font-family: "Bodoni Moda", serif; font-weight: 700; font-size: 16px; padding: 0 28px; display: flex; align-items: center; white-space: nowrap; }

  /* Cover side */
  .hero { position: absolute; left: 0; top: 0; width: 560px; height: 330px; background: var(--navy); }
  .hero__photo { position: absolute; left: 20px; top: 20px; right: 0; bottom: 0; }
  .hero__headline { position: absolute; left: 44px; top: 36px; font-family: "Bodoni Moda", serif; font-weight: 700; font-size: 42px; line-height: 1.05; color: #fff; text-shadow: 0 1px 3px rgba(0,0,0,.35); }
  .offer { position: absolute; left: 590px; top: 24px; width: 180px; height: 290px; background: var(--tan); color: #fff; font-family: "Bodoni Moda", serif; font-weight: 700; font-size: 17px; line-height: 1.3; text-align: center; display: flex; flex-direction: column; justify-content: center; padding: 16px; }
  .offer__rule { width: 40px; height: 1px; background: #fff; margin: 16px auto; }
  .gallery { position: absolute; left: 790px; top: 24px; width: 190px; display: flex; flex-direction: column; gap: 10px; }
  .gallery__item { height: 90px; border: 5px solid #fff; box-shadow: 0 1px 3px rgba(0,0,0,.15); }

  .front-footer { position: absolute; left: 0; right: 0; bottom: 0; height: 114px; display: flex; align-items: center; }
  .brand { display: flex; align-items: center; gap: 12px; padding-left: 40px; width: 300px; }
  .brand__mark { width: 16px; height: 16px; background: var(--navy); flex: none; }
  .brand__name { font-family: "Bodoni Moda", serif; font-weight: 700; font-size: 24px; color: var(--navy); letter-spacing: .03em; white-space: nowrap; }
  .cta { flex: 1; }
  .cta__lead { font-size: 13px; font-weight: 300; color: var(--muted); }
  .cta__web { font-family: "Bodoni Moda", serif; font-weight: 700; font-size: 20px; color: var(--navy); white-space: nowrap; }
  .phone { width: 260px; height: 100%; background: var(--tan); color: #fff; font-family: "Bodoni Moda", serif; font-weight: 700; font-size: 30px; letter-spacing: .03em; display: flex; align-items: center; justify-content: center; white-space: nowrap; }
</style>
</head>
<body>

<section class="rack-card rack-card--back" aria-label="Rack card, project side">
  <div class="projects">
    <article class="project">
      <div class="project__photo photo" role="img" aria-label="Rendering of a two-storey modern craftsman house with landscaped front yard"></div>
      <h2 class="project__label">Hillcrest Modern Classic</h2>
      <ul class="project__specs">
        <li>Bedrooms 8</li>
        <li>Bathrooms 8</li>
        <li>Main Floor 2,140 Sqft</li>
        <li>Upper Floor 1,860 Sqft</li>
        <li class="total">Total 5,410 Sqft</li>
      </ul>
    </article>
    <article class="project">
      <div class="project__photo photo" role="img" aria-label="Rendering of a dark grey traditional craftsman house"></div>
      <h2 class="project__label">Cedar Lane Traditional</h2>
      <ul class="project__specs">
        <li>Bedrooms 7</li>
        <li>Bathrooms 6</li>
        <li>Main Floor 1,980 Sqft</li>
        <li>Upper Floor 1,720 Sqft</li>
        <li class="total">Total 4,960 Sqft</li>
      </ul>
    </article>
    <article class="project">
      <div class="project__photo photo" role="img" aria-label="Rendering of a large contemporary house at dusk"></div>
      <h2 class="project__label">Westridge Estate</h2>
      <ul class="project__specs">
        <li>Bedrooms 6</li>
        <li>Bathrooms 6</li>
        <li>Main Floor 1,974 Sqft</li>
        <li>Upper Floor 1,602 Sqft</li>
        <li class="total">Total 5,392 Sqft</li>
      </ul>
    </article>
  </div>
  <footer class="back-footer">
    <div class="back-footer__spacer"></div>
    <div class="back-footer__web">www.brindle-homes.ca</div>
  </footer>
</section>

<section class="rack-card rack-card--front" aria-label="Rack card, cover side">
  <div class="hero">
    <div class="hero__photo photo" role="img" aria-label="Rendering of a stone and shingle craftsman home with purple garden plantings"></div>
    <h1 class="hero__headline">Build the<br>home of<br>your dreams.</h1>
  </div>

  <div class="offer">
    <p>High Quality Custom Houses at Affordable Prices.</p>
    <div class="offer__rule"></div>
    <p>Fixed Price Packages Available.</p>
  </div>

  <div class="gallery">
    <div class="gallery__item photo" role="img" aria-label="Small rendering of a grey modern house"></div>
    <div class="gallery__item photo" role="img" aria-label="Small rendering of a blue-sided family house"></div>
    <div class="gallery__item photo" role="img" aria-label="Small rendering of a cream contemporary house"></div>
  </div>

  <footer class="front-footer">
    <div class="brand">
      <span class="brand__mark"></span>
      <span class="brand__name">BRINDLE HOMES</span>
    </div>
    <div class="cta">
      <p class="cta__lead">Learn more about our recent projects at</p>
      <p class="cta__web">www.brindle-homes.ca</p>
    </div>
    <div class="phone">604.555.0148</div>
  </footer>
</section>

</body>
</html>
```